Financial Advisor Resource Firm needs business card design

Need business card design for company in Omaha NE called Meridale Circle. We provide resources to financial advisors....workshop programs, retirement analysis, and insurance planning. I would like to see designs that use grays, greens, black, and white colors. The final design should communicate 'collaboration' and be simple yet attractive to financial planning clients. I will attached our logo and another picture of a puzzle piece coming together. I would like the incorporate the puzzle picture somehow, maybe on the back somehow, with color or just the gray scale....OR, the picture be the front of the card with 'Meridale' definition on it (see upload) and then company logo, employee name, title, address on the back (see ppt uploaded). The following disclosure needs to be included somewhere- Advisory services offered through Stonebrook Assets, LLC.
Updates

I uploaded a svg and ai file of the logo

Target Market(s)

Financial planning clients and financial advisors....so pretty diverse age range of about 40-70.

Industry/Entity Type

Financial Planning

Contact Information for Business Card

Tobias L. Fenwright, MBA
Founder/President
5287 E. Larkin Road
Suite 230
Omaha, NE 68190
Phone- (402) 555-0147
Cell- (402) 555-0183
Fax- (402) 555-0129
email- tobias@meridaleplan.example
web address- www.meridaleplan.example

Colors
1b1b1b
474747
d3d3d3
ffffff
9bcb3c
abd036

Requirements
Must have
• Must include logo provided, must be 2 sided, and must have disclosure...all of these items listed in project description

```html
<!DOCTYPE html>
<html lang="en">
<head>
<meta charset="utf-8">
<title>Meridale Circle – Business Card</title>
<link rel="stylesheet" href="https://fonts.googleapis.com/css2?family=Roboto:wght@400;500;700&display=swap">
<style>
  :root {
    --ink: #1b1b1b;
    --charcoal: #474747;
    --silver: #d3d3d3;
    --paper: #ffffff;
    --leaf: #9bcb3c;
    --lime: #7db52a;
    --moss-light: #b5d08a;
    --moss: #8cb35a;
    --moss-dark: #5f8a32;
    --stage: #3a3a3c;
  }
  * { box-sizing: border-box; margin: 0; padding: 0; }
  html, body {
    width: 1200px; height: 1000px; overflow: hidden;
    background: var(--stage);
    font-family: "Roboto", Arial, sans-serif;
  }
  .canvas { position: relative; width: 1200px; height: 1000px; }

  .card {
    position: absolute;
    width: 640px; height: 366px;
    border-radius: 22px;
    overflow: hidden;
    box-shadow: 0 14px 30px rgba(0,0,0,.35);
  }

  /* Front */
  .card--front { left: 440px; top: 80px; }
  .front-photo {
    position: absolute; inset: 0;
    background:
      radial-gradient(ellipse at 70% 75%, var(--moss-dark) 0%, transparent 55%),
      radial-gradient(ellipse at 25% 30%, var(--moss-light) 0%, transparent 60%),
      linear-gradient(135deg, var(--moss-light) 0%, var(--moss) 55%, var(--moss-dark) 100%);
  }
  .front-band {
    position: absolute; left: 0; right: 0; top: 80px; height: 190px;
    background: rgba(255,255,255,.42);
  }
  .front-brand {
    position: absolute; left: 0; right: 0; top: 130px;
    display: flex; align-items: center; justify-content: center; gap: 14px;
  }
  .brand-dot {
    width: 30px; height: 30px; border-radius: 50%;
    background: var(--lime);
  }
  .brand-name {
    font-weight: 700; color: var(--ink);
    font-size: 48px; letter-spacing: 1px; text-transform: uppercase;
  }
  .front-tagline {
    position: absolute; left: 0; right: 0; top: 290px;
    text-align: center; color: var(--paper);
    font-size: 19px; font-weight: 500;
  }

  /* Back */
  .card--back { left: 120px; top: 520px; background: var(--paper); }
  .back-brand {
    position: absolute; left: 36px; top: 34px;
    display: flex; align-items: center; gap: 10px;
  }
  .back-brand .brand-dot { width: 22px; height: 22px; }
  .back-brand .brand-name { font-size: 34px; }
  .person-name {
    position: absolute; left: 36px; top: 98px;
    color: var(--lime); font-weight: 700; font-size: 22px; letter-spacing: .5px;
  }
  .person-name small { font-size: 15px; }
  .person-title {
    position: absolute; left: 36px; top: 126px;
    color: var(--ink); font-size: 15px;
  }
  .title-rule {
    position: absolute; left: 36px; top: 154px;
    width: 64px; height: 2px; background: var(--lime);
  }
  .contact {
    position: absolute; left: 36px; top: 172px;
    color: var(--ink); font-size: 15px; line-height: 21px;
    list-style: none;
  }
  .contact li { display: flex; align-items: center; gap: 7px; }
  .contact .address { display: block; }
  .contact svg { width: 13px; height: 13px; fill: var(--lime); flex: none; }
  .disclosure {
    position: absolute; left: 36px; bottom: 18px;
    width: 330px;
    color: var(--charcoal); font-size: 10.5px; line-height: 14px;
  }
  .web {
    position: absolute; right: 36px; bottom: 40px;
    display: flex; align-items: center; gap: 7px;
    color: var(--ink); font-size: 15px;
  }
  .web svg { width: 14px; height: 14px; stroke: var(--charcoal); fill: none; stroke-width: 1.4; }
  .web-bar {
    position: absolute; right: 0; bottom: 0;
    width: 250px; height: 26px; background: var(--lime);
  }
</style>
</head>
<body>
<div class="canvas">

  <section class="card card--front">
    <div class="front-photo" role="img" aria-label="Green-tinted photo of hands fitting puzzle pieces together"></div>
    <div class="front-band"></div>
    <div class="front-brand">
      <span class="brand-dot"></span>
      <span class="brand-name">Meridale Circle</span>
    </div>
    <p class="front-tagline">to come together and unite in common interest and focus</p>
  </section>

  <section class="card card--back">
    <div class="back-brand">
      <span class="brand-dot"></span>
      <span class="brand-name">Meridale Circle</span>
    </div>
    <h1 class="person-name">TOBIAS L. FENWRIGHT, <small>MBA</small></h1>
    <p class="person-title">Founder/President</p>
    <div class="title-rule"></div>
    <ul class="contact">
      <li class="address">5287 E. Larkin Road<br>Suite 230 Omaha, NE 68190</li>
      <li><svg viewBox="0 0 24 24"><path d="M6.6 10.8a15 15 0 0 0 6.6 6.6l2.2-2.2a1 1 0 0 1 1-.25 11.4 11.4 0 0 0 3.6.57 1 1 0 0 1 1 1V20a1 1 0 0 1-1 1A17 17 0 0 1 3 4a1 1 0 0 1 1-1h3.5a1 1 0 0 1 1 1c0 1.25.2 2.45.57 3.570a1 1 0 0 1-.25 1z"/></svg>(402) 555-0147</li>
      <li><svg viewBox="0 0 24 24"><path d="M7 1h10a2 2 0 0 1 2 2v18a2 2 0 0 1-2 2H7a2 2 0 0 1-2-2V3a2 2 0 0 1 2-2zm0 3v14h10V4zm5 15.5a1 1 0 1 0 0 2 1 1 0 0 0 0-2z"/></svg>(402) 555-0183</li>
      <li><svg viewBox="0 0 24 24"><path d="M6 2h10l2 2v5H6zM4 10h16a2 2 0 0 1 2 2v6h-4v4H6v-4H2v-6a2 2 0 0 1 2-2zm4 6v4h8v-4z"/></svg>(402) 555-0129</li>
      <li><svg viewBox="0 0 24 24"><path d="M2 5h20v14H2zm2 2v.5l8 5 8-5V7zm0 2.8V17h16V9.8l-8 5z"/></svg>tobias@meridaleplan.example</li>
    </ul>
    <p class="disclosure">Advisory services offered through Stonebrook Assets, LLC.</p>
    <div class="web">
      <svg viewBox="0 0 16 16"><circle cx="8" cy="8" r="6.5"/><ellipse cx="8" cy="8" rx="3" ry="6.5"/><path d="M1.5 8h13M2.5 5h11M2.5 11h11"/></svg>
      www.meridaleplan.example
    </div>
    <div class="web-bar"></div>
  </section>

</div>
</body>
</html>
```